Life Coaching business needs a new flyer

We are an Australian business that specialises in Life Coaching, Career Coaching, Health and Wellness Coaching, Yoga and Pilates. We need a A4 double sided flyer that is full colour and folded to DL format. I have attached a couple of designs that I like and some pictures and would like the flyer to be bright yet stylish.

Industry/Entity Type

Life Coaching

```html
<!DOCTYPE html>
<html lang="en">
<head>
<meta charset="utf-8">
<title>Bright Path Coaching – DL Brochure</title>
<link href="https://fonts.googleapis.com/css2?family=Arimo:wght@400;700&family=Cinzel:wght@400;600&family=Roboto+Condensed:wght@400;700&display=swap" rel="stylesheet">
<style>
  :root {
    --blue: #1a9ad9;
    --green: #5bbf21;
    --ink: #1e1e1e;
    --charcoal: #2b2b2b;
    --paper: #ffffff;
    --backdrop: #ebe8e4;
  }
  * { margin: 0; padding: 0; box-sizing: border-box; }
  html, body { width: 1200px; height: 888px; overflow: hidden; }
  body { background: var(--backdrop); font-family: "Arimo", Arial, sans-serif; color: var(--ink); }

  .spread {
    position: absolute; left: 60px; top: 59px;
    width: 1080px; height: 770px;
    background: var(--paper);
    box-shadow: 0 4px 18px rgba(0,0,0,.18);
    overflow: hidden;
  }
  .spread-art { position: absolute; inset: 0; }

  /* Panel 1 – testimonials */
  .testimonials-title {
    position: absolute; left: 0; top: 13px; width: 348px; height: 36px;
    background: var(--blue); border-radius: 0 18px 18px 0;
    color: #fff; font-family: "Cinzel", Georgia, serif; font-weight: 600;
    font-size: 17px; line-height: 36px; padding-left: 28px; letter-spacing: .3px;
  }
  .testimonial-list { position: absolute; left: 30px; top: 60px; width: 318px; }
  .testimonial { font-size: 10.6px; line-height: 12.6px; text-align: justify; margin-bottom: 4px; }
  .testimonial cite { display: block; text-align: right; font-style: italic; font-weight: 700; margin-top: 5px; }

  /* Panel 2 – intro & offer */
  .intro { position: absolute; left: 380px; top: 40px; width: 324px; text-align: center; font-size: 13.4px; line-height: 16px; }
  .intro p + p { margin-top: 14px; }
  .brand-mark { position: absolute; display: flex; flex-direction: column; align-items: center; }
  .brand-mark .dot { width: 34px; height: 34px; border-radius: 50%; background: var(--green); flex: none; }
  .brand-name {
    font-family: "Cinzel", Georgia, serif; font-weight: 400; color: var(--blue);
    text-align: center; line-height: 1.15;
  }
  .brand-mark--centre { left: 380px; top: 214px; width: 324px; gap: 8px; }
  .brand-mark--centre .brand-name { font-size: 18px; }

  .offer { position: absolute; left: 392px; top: 556px; width: 304px; text-align: center; font-family: "Roboto Condensed", Arial, sans-serif; }
  .offer-title { color: var(--blue); font-weight: 700; font-size: 19px; line-height: 22px; }
  .offer-detail { color: #fff; font-weight: 700; font-size: 17.5px; line-height: 21px; margin-top: 3px; }
  .contact { position: absolute; left: 390px; top: 672px; width: 310px; color: #fff; font-size: 15px; line-height: 19px; }
  .contact li { list-style: none; display: flex; align-items: center; justify-content: center; gap: 6px; }
  .contact svg { width: 12px; height: 12px; flex: none; }

  /* Panel 3 – cover */
  .brand-mark--cover { left: 748px; top: 36px; width: 320px; flex-direction: row; gap: 12px; }
  .brand-mark--cover .dot { width: 56px; height: 56px; }
  .brand-mark--cover .brand-name { font-size: 17px; text-align: left; }
  .cover-title { position: absolute; left: 720px; top: 116px; width: 360px; text-align: center; font-family: "Cinzel", Georgia, serif; }
  .cover-title h1 { color: var(--blue); font-weight: 600; font-size: 25px; letter-spacing: .5px; }
  .cover-title p { color: #3a3a3a; font-size: 20px; margin-top: 2px; }
  .cover-title .sep { color: var(--blue); }
</style>
</head>
<body>
<main class="spread">
  <svg class="spread-art" viewBox="0 0 1080 770" width="1080" height="770">
    <defs>
      <linearGradient id="groupPhoto" x1="0" y1="0" x2="1" y2="1">
        <stop offset="0" stop-color="#cfe0ea"/>
        <stop offset=".45" stop-color="#b9785c"/>
        <stop offset="1" stop-color="#6d7f93"/>
      </linearGradient>
      <linearGradient id="coachPhoto" x1="0" y1="0" x2="1" y2="0">
        <stop offset="0" stop-color="#3b2a26"/>
        <stop offset=".5" stop-color="#c9a08a"/>
        <stop offset="1" stop-color="#8aa0b6"/>
      </linearGradient>
      <linearGradient id="familyPhoto" x1="0" y1="0" x2="0" y2="1">
        <stop offset="0" stop-color="#a9cbe8"/>
        <stop offset=".5" stop-color="#c99a7a"/>
        <stop offset="1" stop-color="#7a5238"/>
      </linearGradient>
      <clipPath id="coverCircle"><circle cx="880" cy="530" r="205"/></clipPath>
    </defs>

    <rect class="photo photo--group" role="img" aria-label="Photo of a group of smiling friends cheering outdoors by the sea" x="0" y="470" width="420" height="300" fill="url(#groupPhoto)"/>
    <path d="M0 466 L0 525 C120 495 260 478 420 474 L420 466 Z" fill="var(--paper)"/>
    <path class="swoosh" d="M0 520 C130 485 270 466 420 470 L420 484 C270 482 130 502 0 548 Z" fill="var(--green)"/>

    <rect class="photo photo--coaches" role="img" aria-label="Portrait photo of the two coaches, a woman and a man" x="404" y="322" width="262" height="170" fill="url(#coachPhoto)"/>

    <path class="offer-panel" d="M392 486 C500 472 620 486 697 512 L697 630 Q697 650 677 650 L412 650 Q392 650 392 630 Z" fill="var(--charcoal)"/>
    <rect x="365" y="650" width="357" height="120" fill="var(--blue)"/>

    <line x1="365" y1="0" x2="365" y2="466" stroke="#e6e6e6"/>
    <line x1="722" y1="0" x2="722" y2="770" stroke="#dcdcdc"/>

    <path d="M712 430 A230 230 0 0 1 1090 380" fill="none" stroke="var(--green)" stroke-width="12" transform="translate(0,-40)"/>
    <circle cx="880" cy="530" r="212" fill="var(--paper)"/>
    <rect class="photo photo--family" role="img" aria-label="Photo of a happy family with two children on a sunny beach" x="675" y="325" width="410" height="410" fill="url(#familyPhoto)" clip-path="url(#coverCircle)"/>
    <path d="M722 700 C860 750 990 725 1080 650 L1080 770 L722 770 Z" fill="var(--blue)"/>
    <path d="M722 728 C860 762 990 748 1080 695 L1080 770 L722 770 Z" fill="var(--green)"/>
  </svg>

  <h2 class="testimonials-title">HAPPY CLIENTS TESTIMONIALS</h2>
  <section class="testimonial-list">
    <blockquote class="testimonial">“I have lost 10 kilos and now have the energy to play with my kids. Thanks Mara for your support/guidance and helping me get rid of my limiting beliefs. I feel I can achieve anything now! The sky’s the limit”<cite>Leah, Northbridge</cite></blockquote>
    <blockquote class="testimonial">“I had always wanted to start up own café however every time it came to putting it into practice I would procrastinate and not achieve anything. I became overwhelmed with the whole process and never achieved anything. Mara put it into bite sized chunks and helped me to set small achievable goals. I am now a happy café owner.”<cite>Tessa, Rose Bay</cite></blockquote>
    <blockquote class="testimonial">“Mara has helped to change my life around in all aspects. I would have been lost without her. Thanks Mara for your professionalism, support and guidance.”<cite>Carla, Neutral Bay</cite></blockquote>
    <blockquote class="testimonial">“I was so busy with kids, work, and my husband I lost who I was. Mara has helped me find the person I am again.”<cite>Holly, Lane Cove</cite></blockquote>
    <blockquote class="testimonial">“When I started with Coach Mara, I didn’t know anything about coaching. I called her because she helped a friend of mine make a career change that was a perfect fit for her. I had the opportunity to make a change too and did not know where to start. I am now in a job that I love. I would recommend Mara to everyone.”<cite>Daniel, Ohio America</cite></blockquote>
  </section>

  <section class="intro">
    <p>Bright Path Coaching &amp; Meditation Studio is a professional service that can help you achieve the goals that you are looking for in Life Coaching, Meditation, and Yoga/Pilates.</p>
    <p>If you are ready to take your life to the next level and would like to know more,<br>PLEASE CONTACT US.</p>
  </section>
  <div class="brand-mark brand-mark--centre">
    <span class="dot"></span>
    <span class="brand-name">Bright Path<br>Coaching &amp; Meditation Studio</span>
  </div>

  <section class="offer">
    <p class="offer-title">FREE INTRODUCTORY<br>LIFE COACHING</p>
    <p class="offer-detail">Phone/Video session - 20 mins<br>(To see if coaching is right for you)</p>
  </section>
  <ul class="contact">
    <li><svg viewBox="0 0 12 12"><path d="M3 1 L5 3.5 L4 5 Q5 7 7 8 L8.5 7 L11 9 L9.5 11 Q4 10.5 1 3 Z" fill="#fff"/></svg>02 9000 4417</li>
    <li><svg viewBox="0 0 12 12"><rect x="1" y="2.5" width="10" height="7" fill="#fff"/><path d="M1 2.5 L6 7 L11 2.5" fill="none" stroke="#1a9ad9" stroke-width="1"/></svg>hello@brightpathcoaching.com.au</li>
    <li><svg viewBox="0 0 12 12"><circle cx="6" cy="6" r="5" fill="#fff"/></svg>www.brightpathcoaching.com.au</li>
  </ul>

  <div class="brand-mark brand-mark--cover">
    <span class="dot"></span>
    <span class="brand-name">Bright Path<br>Coaching &amp; Meditation</span>
  </div>
  <header class="cover-title">
    <h1>LIFE COACHING</h1>
    <p>MEDITATION <span class="sep">•</span> YOGA/PILATES</p>
  </header>
</main>
</body>
</html>
```